Business card design for a dynamic IT consulting company

We need a business card design for a young firm, specialized in the Telecommunications/Consulting industry. The name of the company is Quindor and Partners Business Consulting Ltd. (Short name: Quindor and Partnes)
Quindor = solve read reverse, so we aim to be uncomplicated and solution-oriented. The small pipe in our logo is also related to the word solve. So we need a new business card design, which is simple, eye catching and something non traditional (I would probably prefer a square shaped design rather than a rectangle, but open for suggestions). Attached our logo.

Target Market(s)

Usually our customers are Tier1 Telecoms providers (Q-Netra, Palorix, etc) and their executives.

Industry/Entity Type

Business

Contact Information for Business Card

Name: Bence Tolnavari
Email: b.tolnavari@quindor.hu
Web: www.quindor.hu
Mobile: +36 30 518 2769
Title: Managing Director

Optional:
Company name: Quindor and Partners Ltd.
Address: 1087 Budapest, Tolvenka str. 28/C, Hungary

Font styles to use
Other font styles liked:
• helveticaneue_medium, Prime Regular are used now.

Colors

Designer to choose colors to be used in the design.

Requirements
Must have
• I would like to have a 2 sided design.
Nice to have
• I thought if we make the logo a bit bigger (without the company name), that could go to the back with the company name below. I though, if the pipe in the logo is somehow touchable on the business card, would be nice and unique.

```html
<!DOCTYPE html>
<html lang="en">
<head>
<meta charset="utf-8">
<title>Quindor and Partners – Business Card</title>
<link rel="stylesheet" href="https://fonts.googleapis.com/css2?family=Arimo:wght@400;500&family=Saira:wght@500;600&display=swap">
<style>
  :root {
    --stage: #2e2825;
    --card: #161616;
    --card-edge: #222;
    --silver: #b9b9b9;
    --silver-dim: #8a8a8a;
    --white: #f2f2f2;
    --magenta: #b5339a;
    --cyan: #1c9ad6;
    --text-soft: #d8d8d8;
  }
  * { margin: 0; padding: 0; box-sizing: border-box; }
  html, body { width: 1200px; height: 780px; overflow: hidden; }
  body {
    background: var(--stage);
    font-family: "Arimo", Helvetica, Arial, sans-serif;
    position: relative;
  }
  .card {
    position: absolute;
    top: 236px;
    width: 540px;
    height: 308px;
    background: var(--card);
    border: 1px solid var(--card-edge);
    border-radius: 4px;
    box-shadow: 0 14px 30px rgba(0,0,0,.45);
  }
  .card--front { left: 40px; }
  .card--back  { left: 620px; }

  /* front */
  .front-brand {
    position: absolute;
    left: 0; right: 0; top: 98px;
    display: flex; align-items: center; justify-content: center; gap: 14px;
  }
  .brand-square {
    width: 22px; height: 22px;
    background: var(--silver);
  }
  .front-brand__name {
    font-family: "Saira", sans-serif;
    font-weight: 500;
    font-size: 40px;
    color: var(--silver);
    letter-spacing: .5px;
  }
  .front-tagline {
    position: absolute;
    left: 0; right: 0; top: 160px;
    text-align: center;
    font-size: 10px;
    letter-spacing: 6px;
    color: var(--silver-dim);
  }
  .front-web {
    position: absolute;
    left: 0; right: 0; top: 218px;
    text-align: center;
    font-size: 14px;
    letter-spacing: 2px;
    color: var(--text-soft);
  }

  /* back */
  .back-brand {
    position: absolute;
    left: 52px; top: 120px;
    width: 170px;
    display: flex; align-items: center; gap: 10px;
  }
  .back-brand .brand-square { background: var(--magenta); width: 18px; height: 18px; }
  .back-brand__name {
    font-family: "Saira", sans-serif;
    font-weight: 600;
    font-size: 30px;
    color: var(--white);
  }
  .back-divider {
    position: absolute;
    left: 240px; top: 80px;
    width: 1px; height: 112px;
    background: var(--magenta);
  }
  .contact {
    position: absolute;
    left: 262px; top: 84px;
  }
  .contact__name {
    font-family: "Saira", sans-serif;
    font-weight: 600;
    font-size: 20px;
    color: var(--white);
    letter-spacing: .5px;
    line-height: 1.1;
  }
  .contact__title {
    font-size: 13px;
    color: var(--magenta);
    margin-bottom: 8px;
  }
  .contact__line {
    display: flex; align-items: center; gap: 8px;
    font-size: 13px;
    color: var(--text-soft);
    line-height: 19px;
  }
  .contact__line svg { width: 12px; height: 12px; flex: none; }
  .address {
    position: absolute;
    left: 52px; bottom: 56px;
    font-size: 14px;
    color: var(--text-soft);
  }
</style>
</head>
<body>

  <section class="card card--front" aria-label="Card front">
    <div class="front-brand">
      <span class="brand-square"></span>
      <span class="front-brand__name">Quindor &amp; Partners</span>
    </div>
    <p class="front-tagline">CLARITY · FOCUS · DRIVE</p>
    <p class="front-web">www.quindor.hu</p>
  </section>

  <section class="card card--back" aria-label="Card back">
    <div class="back-brand">
      <span class="brand-square"></span>
      <span class="back-brand__name">Quindor</span>
    </div>
    <div class="back-divider"></div>

    <div class="contact">
      <p class="contact__name">Bence Tolnavari</p>
      <p class="contact__title">Managing Director</p>
      <p class="contact__line">
        <svg viewBox="0 0 12 12" aria-hidden="true"><rect x="2.5" y="0.5" width="7" height="11" rx="1" fill="none" stroke="var(--magenta)" stroke-width="1.2"/><circle cx="6" cy="9.5" r=".8" fill="var(--magenta)"/></svg>
        +36 30 518 2769
      </p>
      <p class="contact__line">
        <svg viewBox="0 0 12 12" aria-hidden="true"><rect x="0.5" y="2" width="11" height="8" fill="var(--white)"/><path d="M0.5 2 L6 6.5 L11.5 2" fill="none" stroke="var(--card)" stroke-width="1"/></svg>
        b.tolnavari@quindor.hu
      </p>
      <p class="contact__line">
        <svg viewBox="0 0 12 12" aria-hidden="true"><circle cx="6" cy="6" r="5.5" fill="var(--cyan)"/><path d="M0.5 6 H11.5 M6 0.5 V11.5 M6 0.5 C3 3 3 9 6 11.5 M6 0.5 C9 3 9 9 6 11.5" fill="none" stroke="var(--card)" stroke-width=".7"/></svg>
        www.quindor.hu
      </p>
    </div>

    <p class="address">1087 Budapest, Tolvenka str. 28/C, Hungary</p>
  </section>

</body>
</html>
```